Alloy wheel repair business needs a website

Install logo previously purchased from makerhive, toolbar with dropdowns. services, gallery, clients , contact ect
Maybe mission statment

Target Market(s)

vehicle owners, auto dealers,insurance companies,

Industry/Entity Type

Alloy Wheel Repair

Coding

Coded - Design and coding required

Number of Pages Required

4 page

Font styles to use
Sans Serif

Colors
0054AA
0677BA
7BADD7
CADEEF
E8F1F8

```html
<!DOCTYPE html>
<html lang="en">
<head>
<meta charset="utf-8">
<title>Rimforge Wheelcare – Alloy Wheel Repair</title>
<link rel="stylesheet" href="https://fonts.googleapis.com/css2?family=Michroma&family=Manrope:wght@400;500;600;700&display=swap">
<style>
:root{
  --blue-deep:#0054AA;
  --blue:#0677BA;
  --blue-mid:#4a8acb;
  --blue-soft:#7BADD7;
  --blue-pale:#CADEEF;
  --blue-mist:#E8F1F8;
  --ink:#111418;
  --text:#3a3f46;
  --night:#050d1a;
  --white:#ffffff;
}
*{box-sizing:border-box;margin:0;padding:0}
html,body{width:1200px;height:4831px;overflow:hidden;background:var(--white)}
body{position:relative;font-family:"Manrope",sans-serif;color:var(--text)}
.abs{position:absolute}
.display{font-family:"Michroma",sans-serif;text-transform:uppercase;letter-spacing:2px;white-space:nowrap}
.section-mark{position:absolute;left:586px;width:28px;height:28px;border-radius:50%;background:var(--ink)}
.section-title{position:absolute;left:0;width:1200px;text-align:center;font-family:"Michroma",sans-serif;font-size:24px;color:var(--blue-mid);text-transform:uppercase;letter-spacing:2px;white-space:nowrap}
.photo{position:absolute;border-radius:14px}
.btn{position:absolute;display:flex;align-items:center;justify-content:center;border-radius:34px;font-family:"Michroma",sans-serif;font-size:16px;text-transform:uppercase;letter-spacing:1.5px;color:var(--white);background:var(--blue-mid);white-space:nowrap}
.body-copy{position:absolute;font-size:15.5px;line-height:33.5px;text-align:justify;color:var(--text)}

/* hero */
.hero{position:absolute;left:0;top:0;width:1200px;height:675px;background:radial-gradient(ellipse at 30% 35%,#5a6068 0%,#2c3036 45%,#15181c 100%)}
.hero-tyres{position:absolute;left:120px;top:130px;width:340px;height:545px;background:linear-gradient(180deg,#1d1f22,#0c0d0f);border-radius:40px 40px 0 0}
.navbox{position:absolute;left:192px;top:15px;width:817px;height:111px;background:var(--white)}
.topbar{position:absolute;left:235px;top:0;width:582px;height:51px;background:var(--ink);display:flex;align-items:center;gap:56px;padding-left:54px;color:var(--white);font-size:13px;font-weight:600}
.topbar span{display:flex;align-items:center;gap:12px}
.brand{position:absolute;left:34px;top:30px;display:flex;align-items:center;gap:8px;font-family:"Michroma",sans-serif;font-size:22px;color:var(--blue-deep);text-transform:uppercase;line-height:1}
.brand i{width:14px;height:14px;border-radius:50%;background:var(--blue-deep);display:block}
.brand small{display:block;font-size:9px;letter-spacing:3px;margin-top:6px}
.nav{position:absolute;left:277px;top:70px;display:flex;gap:29px;font-size:15px;font-weight:600;color:var(--ink)}
.nav .active{color:var(--blue-mid);border-bottom:2px solid var(--blue-mid);padding-bottom:4px}
.hero-kicker{left:540px;top:206px;font-size:24px;color:var(--white)}
.hero-title{left:540px;top:256px;font-size:31px;line-height:44px;letter-spacing:1px;color:var(--white)}
.hero-copy{position:absolute;left:540px;top:332px;width:580px;font-size:20.5px;line-height:39px;color:#eef2f6;font-weight:500}
.hero .btn{left:540px;top:521px;width:214px;height:64px;background:var(--ink);font-size:16px}

/* what we do */
.grid{position:absolute;left:171px;top:894px;width:860px;height:554px;display:grid;grid-template-columns:repeat(3,1fr);grid-template-rows:repeat(2,1fr)}
.tile{display:flex;flex-direction:column;align-items:center;justify-content:center;gap:12px;color:var(--white);font-family:"Michroma",sans-serif;font-size:15px;text-transform:uppercase;text-align:center;line-height:41px;letter-spacing:1.5px;white-space:nowrap}
.tile.blue{background:var(--blue-mid)}
.tile.dark{background:#000}

/* services */
.card{position:absolute;top:2299px;width:471px;height:298px;border-radius:12px;overflow:hidden;box-shadow:0 4px 12px rgba(0,0,0,.25)}
.card .txt{position:absolute;left:272px;top:52px;width:185px}
.card h3{font-family:"Michroma",sans-serif;font-size:17px;letter-spacing:1px;margin-bottom:14px;white-space:nowrap;text-transform:uppercase}
.card p{font-size:15px;line-height:31px;font-weight:500}
.card .mini{margin-top:16px;width:120px;height:33px;border-radius:17px;background:var(--blue-mid);color:var(--white);font-family:"Michroma",sans-serif;font-size:9px;display:flex;align-items:center;justify-content:center;letter-spacing:1px;text-transform:uppercase}

/* clients */
.clients{position:absolute;left:0;top:2694px;width:1200px;height:512px;background:radial-gradient(ellipse at 50% 50%,#2a2f36 0%,#111418 65%,#07080a 100%)}
.quote{position:absolute;left:230px;top:284px;width:740px;text-align:center;font-size:15.5px;line-height:31px;color:var(--white);font-weight:500}
.dots{position:absolute;left:570px;top:457px;display:flex;gap:15px}
.dots i{width:8px;height:8px;border-radius:50%;background:var(--white);display:block}
.dots i:first-child{width:11px;height:11px;margin-top:-1px}

/* gallery arrows */
.arrow{position:absolute;top:3773px;width:48px;height:48px;border-radius:50%;background:var(--blue-mid);border:3px solid var(--blue-pale);display:flex;align-items:center;justify-content:center}

/* footer */
.footer{position:absolute;left:0;top:4538px;width:1200px;height:293px;background:var(--night);color:var(--white)}
.footer .brand{left:0;width:1200px;top:54px;justify-content:center;color:var(--white)}
.fnav{position:absolute;left:0;width:1200px;top:132px;display:flex;justify-content:center;gap:31px;font-size:15px;font-weight:600}
.social{position:absolute;left:535px;top:183px;display:flex;gap:18px}
.social i{width:32px;height:32px;border-radius:7px;background:var(--blue-mid);display:block}
.copy{position:absolute;left:0;width:1200px;top:244px;text-align:center;font-size:13px;font-weight:600}
</style>
</head>
<body>

<header class="hero">
  <div class="hero-tyres" role="img" aria-label="Photo of a stack of black tyres topped by a dark alloy wheel"></div>
  <div class="navbox">
    <div class="brand"><i></i><div>Rimforge<small>Wheelcare</small></div></div>
    <div class="topbar">
      <span><svg width="14" height="14" viewBox="0 0 24 24"><path fill="#fff" d="M6.6 10.8a15 15 0 0 0 6.6 6.6l2.2-2.2c.3-.3.7-.4 1-.2 1.1.4 2.3.6 3.6.6.6 0 1 .4 1 1V20c0 .6-.4 1-1 1A17 17 0 0 1 3 4c0-.6.4-1 1-1h3.5c.6 0 1 .4 1 1 0 1.3.2 2.5.6 3.6.1.3 0 .7-.2 1z"/></svg>555-014-2290</span>
      <span><svg width="16" height="12" viewBox="0 0 16 12"><rect x="0.5" y="0.5" width="15" height="11" fill="none" stroke="#fff"/><path d="M1 1l7 6 7-6" fill="none" stroke="#fff"/></svg>HELLO@RIMFORGEWHEELCARE.COM</span>
    </div>
    <nav class="nav"><span class="active">HOME</span><span>SERVICES</span><span>GALLERY</span><span>CLIENTS</span><span>CONTACT</span></nav>
  </div>
  <div class="abs display hero-kicker">Welcome to</div>
  <h1 class="abs display hero-title">Rimforge Wheelcare</h1>
  <p class="hero-copy">Sed ut perspiciatis unde omnis iste natus error sit voluptatem accusantium doloremque laudantium, totam rem aperiam, eaque ipsa quae ab illo inventore veritatis et quasi architecto beatae vitae dicta sunt</p>
  <div class="btn">Get Started</div>
</header>

<!-- What we do -->
<span class="section-mark" style="top:768px"></span>
<h2 class="section-title" style="top:808px">What we do</h2>
<div class="grid">
  <div class="tile blue"><span>Prevention<br>Maintanance</span>
    <svg width="96" height="96" viewBox="0 0 96 96" fill="none" stroke="#fff" stroke-width="3"><circle cx="48" cy="48" r="44"/><rect x="44" y="30" width="24" height="30" rx="2"/><path d="M49 40h14M49 47h14M49 54h10"/><circle cx="34" cy="38" r="7"/><path d="M22 66c2-10 22-10 24 0"/></svg>
  </div>
  <div role="img" aria-label="Close-up photo of a car suspension and brake assembly" style="background:linear-gradient(160deg,#8a8c8e,#3a3c40 60%,#1a1b1d)"></div>
  <div class="tile blue"><span>Most Common<br>Repairs</span>
    <svg width="96" height="90" viewBox="0 0 96 90" fill="none" stroke="#fff" stroke-width="3"><path d="M16 20h18v14H16zM62 20h18v14H62z"/><path d="M34 27h28"/><circle cx="48" cy="58" r="20"/><circle cx="48" cy="58" r="8"/></svg>
  </div>
  <div role="img" aria-label="Photo of a hand on a tyre tread" style="background:linear-gradient(150deg,#3a3d42,#15171a)"></div>
  <div class="tile dark">
    <svg width="100" height="100" viewBox="0 0 100 100" fill="none" stroke="#fff" stroke-width="3.5"><circle cx="50" cy="50" r="30"/><circle cx="50" cy="50" r="14"/><path d="M50 6v12M50 82v12M6 50h12M82 50h12M19 19l8 8M73 73l8 8M81 19l-8 8M27 73l-8 8"/><path d="M40 60l30 30"/></svg>
    <span style="margin-top:8px">Brake<br>Repair &amp; Services</span>
  </div>
  <div role="img" aria-label="Photo of two chrome alloy wheels with tyres" style="background:linear-gradient(135deg,#5a5e63,#202226 70%,#0e0f11)"></div>
</div>

<!-- About us -->
<span class="section-mark" style="top:1542px"></span>
<h2 class="section-title" style="top:1583px">About us</h2>
<p class="body-copy" style="left:111px;top:1663px;width:491px">Lorem ipsum dolor sit amet, consectetur adipiscing elit, sed do eiusmod tempor incididunt ut labore et dolore magna aliqua. Ut enim ad minim veniam, quis nostrud exercitation ullamco laboris nisi ut aliquip ex ea commodo consequat. Duis aute irure dolor in reprehenderit in voluptate velit esse cillum dolore eu fugiat nulla pariatur. Excepteur sint occaecat cupidatat non proident, sunt in culpa qui officia deserunt mollit anim id est laborum. Sed ut perspiciatis unde omnis iste natus error sit voluptatem accusantium doloremque laudantium, totam rem aperiam, eaque</p>
<div class="btn" style="left:386px;top:1988px;width:216px;height:63px">Learn more</div>
<div class="photo" role="img" aria-label="Photo of a technician in an orange jacket working on an alloy wheel in a workshop" style="left:714px;top:1656px;width:375px;height:392px;background:linear-gradient(135deg,#3a4450,#1d232b 50%,#b8561c 85%,#2a2a2a)"></div>
<div class="photo" role="img" aria-label="Photo of two mesh-spoke alloy wheels" style="left:643px;top:1862px;width:203px;height:202px;border:3px solid #fff;background:linear-gradient(135deg,#9aa6b2,#3b4450 60%,#1b2027)"></div>

<!-- Services -->
<span class="section-mark" style="top:2164px"></span>
<h2 class="section-title" style="top:2207px">Our services</h2>
<div class="card" style="left:120px;background:linear-gradient(180deg,#f0b522,#f3c67a 60%,#f2b88e)">
  <div class="abs" role="img" aria-label="Photo of a tyre on a yellow display podium" style="left:30px;top:40px;width:230px;height:230px;border-radius:50%;background:radial-gradient(circle,#6b5a40,#2a2218 70%,transparent 72%)"></div>
  <div class="txt" style="color:var(--ink)"><h3>Nemo enim</h3><p>Lorem ipsum dolor sit amet, consectetur adipiscing elit</p><div class="mini">Read more</div></div>
</div>
<div class="card" style="left:609px;background:linear-gradient(135deg,#3a3d42,#111214 55%,#050506)">
  <div class="abs" role="img" aria-label="Photo of a dark alloy wheel with tyre" style="left:0;top:0;width:270px;height:298px;background:radial-gradient(circle at 40% 50%,#6c7076,#25272b 60%,transparent 80%)"></div>
  <div class="txt" style="color:var(--white)"><h3>Nemo enim</h3><p>Lorem ipsum dolor sit amet, consectetur adipiscing elit</p><div class="mini">Read more</div></div>
</div>

<!-- Clients -->
<section class="clients" role="img" aria-label="Dark background photo of a car wheel with a yellow brake caliper">
  <span class="section-mark" style="top:43px;background:var(--white)"></span>
  <h2 class="section-title" style="top:91px;color:var(--white);font-size:23px">What our clients says</h2>
  <div class="abs" role="img" aria-label="Client portrait" style="left:545px;top:148px;width:110px;height:110px;border-radius:50%;border:4px solid var(--blue-pale);background:linear-gradient(180deg,#d8e6f2,#e0763a)"></div>
  <p class="quote">Sed ut perspiciatis unde omnis iste natus error sit voluptatem accusantium doloremque laudantium, totam rem aperiam, eaque ipsa quae ab illo inventore veritatis et quasi architecto beatae vitae dicta sunt explicabo. Nemo enim ipsam voluptatem quia voluptas sit aspernatur aut</p>
  <div class="abs display" style="left:0;width:1200px;top:401px;text-align:center;font-size:18px;color:var(--white)">Lorem ipsum</div>
  <div class="dots"><i></i><i></i><i></i></div>
</section>

<!-- Gallery -->
<span class="section-mark" style="top:3304px"></span>
<h2 class="section-title" style="top:3349px">Our gallery</h2>
<div class="photo" role="img" aria-label="Photo of alloy wheels with orange accents on a rack" style="left:0;top:3444px;width:441px;height:274px;border-radius:0 10px 10px 0;background:linear-gradient(110deg,#cfd2d6,#3a3d42 35%,#1a1b1e 60%,#c7501c 85%,#2a2a2a)"></div>
<div class="photo" role="img" aria-label="Photo of a mechanic holding a tyre in a warm-lit garage" style="left:452px;top:3431px;width:296px;height:300px;background:linear-gradient(160deg,#f0a040,#6a5c50 40%,#2a2c30 80%)"></div>
<div class="photo" role="img" aria-label="Photo of a single tyre standing in a dark workshop" style="left:759px;top:3444px;width:441px;height:274px;border-radius:10px 0 0 10px;background:linear-gradient(180deg,#5a5f66,#1c1e22 60%,#0c0d0f)"></div>
<div class="arrow" style="left:542px"><svg width="12" height="14" viewBox="0 0 12 14"><path d="M8 2L3 7l5 5" fill="none" stroke="#fff" stroke-width="2"/></svg></div>
<div class="arrow" style="left:608px"><svg width="12" height="14" viewBox="0 0 12 14"><path d="M4 2l5 5-5 5" fill="none" stroke="#fff" stroke-width="2"/></svg></div>

<!-- Mission -->
<span class="section-mark" style="top:3923px"></span>
<h2 class="section-title" style="top:3968px">Our mission</h2>
<div class="photo" role="img" aria-label="Photo of a mechanic in a cap fitting a tyre" style="left:112px;top:4035px;width:376px;height:390px;background:linear-gradient(135deg,#6a6e74,#2a2c30 50%,#0e0f11)"></div>
<div class="photo" role="img" aria-label="Photo of a mechanic working on a wheel" style="left:354px;top:4241px;width:203px;height:203px;border:3px solid #fff;background:linear-gradient(135deg,#585c62,#1e2024 60%,#0b0c0e)"></div>
<p class="body-copy" style="left:600px;top:4042px;width:489px">Lorem ipsum dolor sit amet, consectetur adipiscing elit, sed do eiusmod tempor incididunt ut labore et dolore magna aliqua. Ut enim ad minim veniam, quis nostrud exercitation ullamco laboris nisi ut aliquip ex ea commodo consequat. Duis aute irure dolor in reprehenderit in voluptate velit esse cillum dolore eu fugiat nulla pariatur. Excepteur sint occaecat cupidatat non proident, sunt in culpa qui officia deserunt mollit anim id est laborum. Sed ut perspiciatis unde omnis iste natus error sit voluptatem accusantium doloremque laudantium, totam rem aperiam, eaque</p>
<div class="btn" style="left:600px;top:4367px;width:216px;height:64px">Learn more</div>

<!-- Footer -->
<footer class="footer">
  <div class="brand"><i style="background:var(--white)"></i><div>Rimforge<small>Wheelcare</small></div></div>
  <nav class="fnav"><span>HOME</span><span>SERVICES</span><span>GALLERY</span><span>CLIENTS</span><span>CONTACT</span></nav>
  <div class="social" aria-label="Social links"><i></i><i></i><i></i></div>
  <p class="copy">©2023 COPYRIGHTS. RIMFORGE WHEELCARE. ALL RIGHTS RESERVED.</p>
</footer>

</body>
</html>
```